PROPERTY MANAGEMENT AND REAL ESTATE

Target Market(s)

real estate owners and investors

Industry/Entity Type

Real Estate

Contact Information for Business Card

BRIGHT LANTERN PROPERTY MANAGEMENT GROUP, LLC
287 North Willowmere Parkway
Suite 240
Hallandale Beach, FL 33071

```html
<!DOCTYPE html>
<html lang="en">
<head>
<meta charset="utf-8">
<title>Bright Lantern Property Management – Business Card</title>
<link rel="stylesheet" href="https://fonts.googleapis.com/css2?family=Exo+2:wght@400;500;600&family=Saira+Condensed:wght@500&display=swap">
<style>
  :root {
    --stage: #2b2b2b;
    --card-black: #0b0b0b;
    --card-white: #fafafa;
    --brand-red: #a30f12;
    --ink: #2a2a2a;
    --light: #f2f2f2;
  }
  * { margin: 0; padding: 0; box-sizing: border-box; }
  html, body {
    width: 1200px; height: 944px; overflow: hidden;
    background: var(--stage);
    font-family: "Exo 2", sans-serif;
  }
  .canvas { position: relative; width: 1200px; height: 944px; }

  .card {
    position: absolute; top: 112px;
    width: 412px; height: 720px;
    box-shadow: 0 12px 30px rgba(0,0,0,.45);
    overflow: hidden;
  }
  .card-front { left: 150px; }
  .card-back { left: 638px; background: var(--card-black); }

  .card-shapes { position: absolute; inset: 0; }

  .brand {
    position: absolute; left: 0; right: 0; top: 96px;
    display: flex; flex-direction: column; align-items: center;
  }
  .brand-dot {
    width: 64px; height: 64px; border-radius: 50%;
    background: var(--brand-red);
  }
  .brand-name {
    margin-top: 22px;
    font-family: "Exo 2", sans-serif; font-weight: 400;
    font-size: 14px; line-height: 1.35; letter-spacing: .6px;
    color: var(--ink); text-align: center; text-transform: uppercase;
  }

  .person { position: absolute; left: 60px; top: 338px; }
  .person-name {
    font-family: "Saira Condensed", sans-serif; font-weight: 500;
    font-size: 40px; line-height: 1; letter-spacing: 1px;
    color: var(--brand-red);
  }
  .person-title {
    margin-top: 6px;
    font-family: "Exo 2", sans-serif; font-weight: 500;
    font-size: 21px; letter-spacing: 1.6px; color: var(--light);
  }

  .contacts {
    position: absolute; left: 60px; top: 450px; width: 306px;
    list-style: none;
  }
  .contacts li {
    display: flex; align-items: center; gap: 14px;
    min-height: 34px;
    font-size: 15px; letter-spacing: .6px; color: var(--light);
  }
  .contacts li.contact-address {
    align-items: flex-start; padding-top: 6px; line-height: 20px;
  }
  .contact-address .contact-icon { margin-top: -1px; }
  .contact-icon {
    flex: none; width: 22px; height: 22px; border-radius: 50%;
    background: var(--brand-red);
    display: flex; align-items: center; justify-content: center;
  }
  .contact-icon svg { width: 12px; height: 12px; }
</style>
</head>
<body>
<main class="canvas">

  <section class="card card-front" aria-label="Business card front">
    <svg class="card-shapes" width="412" height="720" viewBox="0 0 412 720" aria-hidden="true">
      <rect width="412" height="720" fill="var(--card-black)"/>
      <polygon points="0,0 412,0 412,262 378,300 34,300 0,262" fill="var(--card-white)"/>
      <polygon points="0,262 34,300 34,700 0,700" fill="var(--brand-red)"/>
      <polygon points="412,262 378,300 378,700 412,700" fill="var(--brand-red)"/>
      <rect x="0" y="700" width="412" height="20" fill="var(--card-white)"/>
    </svg>

    <div class="brand">
      <span class="brand-dot"></span>
      <p class="brand-name">Bright Lantern Property<br>Management Group, LLC</p>
    </div>

    <div class="person">
      <h1 class="person-name">DANIEL REYES</h1>
      <p class="person-title">GENERAL MANAGER</p>
    </div>

    <ul class="contacts">
      <li>
        <span class="contact-icon"><svg viewBox="0 0 24 24"><path fill="#fff" d="M6.6 10.8a15 15 0 0 0 6.6 6.6l2.2-2.2c.3-.3.7-.4 1-.2 1.1.4 2.3.6 3.6.6.6 0 1 .4 1 1V20c0 .6-.4 1-1 1A17 17 0 0 1 3 4c0-.6.4-1 1-1h3.5c.6 0 1 .4 1 1 0 1.3.2 2.5.6 3.6.1.3 0 .7-.2 1z"/></svg></span>
        954 555 0142
      </li>
      <li>
        <span class="contact-icon"><svg viewBox="0 0 24 24"><path fill="#fff" d="M6.6 10.8a15 15 0 0 0 6.6 6.6l2.2-2.2c.3-.3.7-.4 1-.2 1.1.4 2.3.6 3.6.6.6 0 1 .4 1 1V20c0 .6-.4 1-1 1A17 17 0 0 1 3 4c0-.6.4-1 1-1h3.5c.6 0 1 .4 1 1 0 1.3.2 2.5.6 3.6.1.3 0 .7-.2 1z"/></svg></span>
        954 555 0187
      </li>
      <li>
        <span class="contact-icon"><svg viewBox="0 0 24 24"><path fill="#fff" d="M3 5h18v14H3z M3 5l9 7 9-7" stroke="#a30f12" stroke-width="1.5"/></svg></span>
        dreyes@brightlanternpm.com
      </li>
      <li>
        <span class="contact-icon"><svg viewBox="0 0 24 24"><g fill="none" stroke="#fff" stroke-width="2"><circle cx="12" cy="12" r="9"/><path d="M3 12h18M12 3c3 3 3 15 0 18M12 3c-3 3-3 15 0 18"/></g></svg></span>
        www.brightlanternpm.com
      </li>
      <li class="contact-address">
        <span class="contact-icon"><svg viewBox="0 0 24 24"><path fill="#fff" d="M12 2a7 7 0 0 0-7 7c0 5 7 13 7 13s7-8 7-13a7 7 0 0 0-7-7zm0 9.5a2.5 2.5 0 1 1 0-5 2.5 2.5 0 0 1 0 5z"/></svg></span>
        <address style="font-style: normal;">287 North Willowmere Parkway<br>Suite 240<br>Hallandale Beach, FL 33071</address>
      </li>
    </ul>
  </section>

  <section class="card card-back" aria-label="Business card back"></section>

</main>
</body>
</html>
```